Need a Wordpress website for my HVAC company

I need a Wordpress website created for an HVAC company in a competitive market.
Following are some websites I like:
My current website is www.borvicoheating.com - we also have a facebook page with some pictures

We are an airconditioning and heating company that does both residential and commmercial work.
We need the following info on our website:
-mobile friendly
-Schedule an appt -repair/maintnenace/installation (i would like this option to always be on the page even if they scroll down.)
-24 hour service
-coupons /promotions
-financing
-reviews/testimonials
-about
-blog
-Our service area
The following are services we provide:
-Air conditioning - Installation/Service/Maintenance/new construction
-Heating - Installation/Service/Maintenance/new construction ( gas furnace, 2 stage furnace, electric heat)
-Duct - Repair/Replacement/Istallation - (zone systems)
-thermostats (wifi)
-Heat pump
-Air handler
-self communicating systems
-carbon monoxide testing
-hail damage
-duct sealing
-insulation
-Air cleaners - UV Air purifiers
-humidifiers

I would also like Quilbo SEO add on

Target Market(s)

Anyone who needs our services HVAC contractor

Industry/Entity Type

Hvac

Contact Information for Business Card

Phone:480-555-2046
website:www.borvicoheating.com
email pmarsh@borvicoheating.com

Coding

Coded - Design and coding required

Number of Pages Required

5+ page

Font styles to use
Serif
Sans Serif

Requirements
Must have
• I wrote in brief. I already have Webly Nest. Long story I paid for 3 years already. I need someone to put website there. Ive never used Wordpress but would like a template page so I can easily add services.
Nice to have
• Clean, bright, original

```html
<!DOCTYPE html>
<html lang="en">
<head>
<meta charset="utf-8">
<title>Borvico Heating Services</title>
<link href="https://fonts.googleapis.com/css2?family=Roboto+Condensed:wght@400;700&family=Open+Sans:wght@400;600;700&display=swap" rel="stylesheet">
<style>
:root{
  --blue:#1f5fa8;
  --blue-dark:#174a86;
  --nav:#1d5b9f;
  --red:#d42430;
  --green:#1e9a4a;
  --ink:#2b2b2b;
  --muted:#777;
  --light:#f3f3f3;
  --line:#dcdcdc;
  --dark:#2c2f33;
  --white:#fff;
}
*{box-sizing:border-box;margin:0;padding:0}
html,body{width:1200px;height:3422px;overflow:hidden}
body{font-family:"Open Sans",Arial,sans-serif;color:var(--ink);background:var(--white);position:relative}
section,header,footer{position:absolute;left:0;width:1200px}
.abs{position:absolute}
.ph{display:block}

/* header */
.site-header{top:0;height:187px;background:var(--white)}
.brand{left:107px;top:42px;display:flex;align-items:center;gap:12px}
.brand-dot{width:44px;height:44px;border-radius:50%;background:var(--red)}
.brand-name{font-family:"Roboto Condensed",sans-serif;font-weight:700;font-size:26px;color:var(--blue);line-height:1.05;width:170px}
.contact-chip{display:flex;align-items:center;gap:12px}
.contact-chip svg{width:36px;height:36px}
.chip-small{font-size:14px;color:var(--muted)}
.chip-big{font-family:"Roboto Condensed",sans-serif;font-size:24px;color:var(--ink)}
.mascot-head{left:1000px;top:11px;width:102px;height:126px;border-radius:8px;background:linear-gradient(#3a7bc8,#1d4f8c)}
.main-nav{left:98px;top:139px;width:1004px;height:48px;background:var(--nav);display:flex;align-items:center}
.main-nav a{font-family:"Roboto Condensed",sans-serif;color:var(--white);text-decoration:none;font-size:14px;padding:0 16px;height:48px;line-height:48px;white-space:nowrap}
.main-nav a.active{background:var(--blue-dark)}
.main-nav .quote{margin-left:auto;background:var(--red);font-size:17px;padding:0 22px;min-width:164px;text-align:center}

/* hero */
.hero{top:187px;height:527px;background:linear-gradient(90deg,#f2f2f2,#e4e6e8 60%,#d8dadc)}
.hero-photo{left:0;top:0;width:740px;height:527px;background:linear-gradient(120deg,#e9ebed,#cfd4da 55%,#b7c1cd)}
.hero-title{left:771px;top:170px;font-family:"Roboto Condensed",sans-serif;font-size:42px;line-height:44px;color:var(--blue);font-weight:700}
.hero-text{left:771px;top:270px;width:330px;font-size:13px;line-height:21px;color:#555}
.btn-outline{display:inline-block;border:2px solid var(--blue);color:var(--blue);font-family:"Roboto Condensed",sans-serif;font-size:13px;padding:7px 14px;border-radius:3px;white-space:nowrap}
.hero .btn-outline{position:absolute;left:771px;top:322px}
.dots{display:flex;gap:8px}
.dots span{width:12px;height:12px;border-radius:50%;background:#555}
.dots span.on{background:var(--blue);box-shadow:0 0 0 3px #c9d9ee}
.hero .dots{position:absolute;left:777px;top:382px}

/* why */
.why{top:714px;height:438px;background:var(--white)}
.sec-title{font-family:"Roboto Condensed",sans-serif;font-size:32px;font-weight:400;color:var(--ink);white-space:nowrap}
.why .sec-title{position:absolute;left:98px;top:56px}
.why-intro{left:98px;top:107px;width:720px;font-size:12px;line-height:20px;color:#666}
.feature{width:270px;display:flex;gap:18px}
.feature svg{flex:none;width:48px;height:48px}
.feature h3{font-family:"Roboto Condensed",sans-serif;font-weight:400;font-size:18px;color:var(--blue);margin-bottom:8px}
.feature p{font-size:11px;line-height:18px;color:#666}
.why-mascot{left:840px;top:40px;width:260px;height:398px;border-radius:120px 120px 12px 12px;background:linear-gradient(#4a87cf,#1f4f8d 65%,#2b3340)}

/* about */
.about{top:1152px;height:438px;background:linear-gradient(#f6f6f6,#ececec)}
.video{left:98px;top:73px;width:500px;height:292px;background:var(--white);border:1px solid var(--line);box-shadow:0 2px 6px rgba(0,0,0,.12)}
.video-art{left:12px;top:10px;width:476px;height:236px;background:linear-gradient(135deg,#e7edf5,#c8d8ec)}
.video-bar{left:12px;top:250px;width:476px;height:26px;background:#3b3b3b;border-radius:2px}
.video-bar i{position:absolute;left:12px;top:11px;width:320px;height:4px;background:#e07a28}
.about .sec-title{position:absolute;left:630px;top:66px;color:#111;font-weight:700}
.about-sub{left:630px;top:112px;font-family:"Roboto Condensed",sans-serif;font-size:22px;color:#333}
.about-text{left:630px;width:470px;font-size:12px;line-height:20px;color:#555}
.about .btn-outline{position:absolute;left:630px;top:320px;border:1px solid #999;color:#444}

/* services */
.services{top:1590px;height:593px;background:var(--white)}
.center-title{width:1200px;text-align:center;top:56px}
.rule{left:563px;top:104px;width:74px;height:3px;background:var(--green)}
.svc{width:300px}
.svc h3{font-family:"Roboto Condensed",sans-serif;font-weight:400;font-size:20px;color:var(--ink);margin-bottom:6px}
.svc p{font-size:11px;line-height:17px;color:#666}
.svc.left{text-align:right}
.svc-icon{width:80px;height:80px;border-radius:50%;background:var(--green);border:4px solid #d6eedd;display:flex;align-items:center;justify-content:center}
.svc-icon svg{width:40px;height:40px}
.van{left:479px;top:205px;width:246px;height:175px;border-radius:16px;background:linear-gradient(#f5f5f5,#d9dde3 70%,#2c3440)}
.btn-green{left:490px;top:500px;width:224px;height:38px;background:var(--green);color:var(--white);font-family:"Roboto Condensed",sans-serif;font-size:15px;text-align:center;line-height:38px;border-radius:2px;white-space:nowrap}

/* testimonial */
.quote-band{top:2183px;height:340px;background:linear-gradient(135deg,#2b6cbd,#1f5aa6 55%,#2a69b8)}
.quote-mark{width:1200px;text-align:center;top:58px;font-family:Georgia,serif;font-size:120px;line-height:100px;color:var(--white);font-weight:700}
.quote-text{left:180px;top:160px;width:840px;text-align:center;color:var(--white);font-size:13px;line-height:20px;font-weight:700}
.quote-name{width:1200px;text-align:center;top:240px;color:var(--white);font-size:17px;font-style:italic;font-family:"Roboto Condensed",sans-serif}
.slide-bars{left:552px;top:284px;display:flex;gap:6px}
.slide-bars span{width:28px;height:3px;background:rgba(255,255,255,.45)}
.slide-bars span.on{background:var(--white)}

/* news */
.news{top:2523px;height:472px;background:var(--white)}
.news .center-title{top:60px}
.card{top:123px;width:319px;height:281px;background:var(--white);box-shadow:0 1px 5px rgba(0,0,0,.18)}
.card-img{width:319px;height:171px}
.date{left:22px;top:181px;background:#2a7fd6;color:var(--white);font-size:10px;padding:4px 8px}
.card h4{position:absolute;left:22px;top:220px;width:280px;font-family:"Roboto Condensed",sans-serif;font-weight:400;font-size:14px;line-height:18px;color:#333}

/* emergency */
.emergency{left:98px;top:2995px;width:1004px;height:99px;background:var(--red);overflow:hidden}
.em-dark{left:680px;top:0;width:360px;height:99px;background:var(--dark);transform:skewX(-25deg)}
.em-thumb{left:14px;top:4px;width:92px;height:95px;border-radius:40px 40px 4px 4px;background:linear-gradient(#4a87cf,#1f4f8d)}
.em-title{left:142px;top:22px;font-family:"Roboto Condensed",sans-serif;font-size:26px;color:var(--white);white-space:nowrap}
.em-sub{left:142px;top:60px;font-size:12px;color:var(--white)}
.em-btn{left:732px;top:30px;width:238px;height:40px;background:var(--blue);color:var(--white);font-family:"Roboto Condensed",sans-serif;font-size:15px;line-height:40px;text-align:center;white-space:nowrap}

/* footer */
.site-footer{top:3094px;height:278px;background:var(--light)}
.foot-brand{left:114px;top:60px;display:flex;align-items:center;gap:10px}
.foot-brand .brand-dot{width:34px;height:34px}
.foot-brand .brand-name{font-size:20px;width:150px}
.socials{left:127px;top:150px;display:flex;gap:8px}
.socials span{width:28px;height:28px;border-radius:50%;border:1px solid #777}
.foot-h{font-family:"Roboto Condensed",sans-serif;font-size:17px;color:#333}
.foot-p{font-size:11px;line-height:18px;color:#666}
.field{left:372px;top:130px;width:245px;height:40px;background:var(--white);border:1px solid var(--line);font-size:11px;color:#888;padding:12px}
.sub-btn{left:372px;top:185px;width:107px;height:38px;background:var(--blue-dark);color:var(--white);font-size:11px;line-height:38px;text-align:center}
.contact-row{display:flex;gap:12px;font-size:12px;line-height:18px;color:#555}
.contact-row svg{flex:none;width:16px;height:16px;margin-top:1px}
.links{left:995px;top:36px}
.links ul{list-style:none;margin-top:14px}
.links li{font-size:11px;line-height:22px;color:#555}
.copyright{top:3372px;height:50px;background:#e8e8e8;border-top:1px solid var(--line);text-align:center;line-height:50px;font-size:11px;color:#666}
</style>
</head>
<body>

<header class="site-header">
  <div class="brand abs"><span class="brand-dot"></span><span class="brand-name">Borvico Heating Services</span></div>
  <div class="contact-chip abs" style="left:548px;top:52px">
    <svg viewBox="0 0 36 36"><circle cx="18" cy="18" r="16" fill="none" stroke="#d42430" stroke-width="2.5"/><path d="M12 10l4 0 2 5-3 2c1 3 3 5 6 6l2-3 5 2v4c-9 1-17-7-16-16z" fill="#d42430"/></svg>
    <div><div class="chip-small">Call Us :</div><div class="chip-big">(480) 555-2046</div></div>
  </div>
  <div class="contact-chip abs" style="left:771px;top:50px">
    <svg viewBox="0 0 36 36"><circle cx="18" cy="20" r="13" fill="none" stroke="#d42430" stroke-width="2.5"/><path d="M18 12v8l5 3" fill="none" stroke="#d42430" stroke-width="2.5"/><path d="M6 8l5-4M30 8l-5-4" stroke="#d42430" stroke-width="2.5"/></svg>
    <div><div class="chip-big">24 hours a day</div><div class="chip-small">7 days a week</div></div>
  </div>
  <div class="mascot-head abs ph" role="img" aria-label="Cartoon technician mascot giving a thumbs up"></div>
  <nav class="main-nav abs">
    <a class="active">HOME</a><a>ABOUT US</a><a>24 HOUR SERVICES</a><a>COUPONS</a><a>FINANCING</a><a>REVIEWS</a><a>BLOG</a><a>CONTACT US</a><a class="quote">REQUEST A QUOTE</a>
  </nav>
</header>

<section class="hero">
  <div class="hero-photo abs ph" role="img" aria-label="Smiling technician giving a thumbs up beside a wall-mounted air conditioner"></div>
  <h1 class="hero-title abs">AIR CONDITIONING<br>AND HEATING</h1>
  <p class="hero-text abs">Borvico Heating Services is the premier residential heating, air conditioning, and energy solutions</p>
  <span class="btn-outline">MORE INFOR ➜</span>
  <div class="dots"><span class="on"></span><span></span><span></span><span></span></div>
</section>

<section class="why">
  <h2 class="sec-title">WHY CHOOSE US</h2>
  <p class="why-intro abs">We keep homes and businesses comfortable all year with honest pricing, quick response and careful work. Every visit is handled by trained staff who respect your time and your home.</p>
  <div class="feature abs" style="left:98px;top:176px">
    <svg viewBox="0 0 48 48"><circle cx="24" cy="24" r="19" fill="none" stroke="#1f5fa8" stroke-width="3"/><text x="24" y="29" text-anchor="middle" font-size="13" font-weight="700" fill="#1f5fa8" font-family="Arial">24</text></svg>
    <div><h3>24/7 Emergency Service</h3><p>You need air conditioning service when you need it, not when we feel like being open. Call now. No need to wait!</p></div>
  </div>
  <div class="feature abs" style="left:479px;top:176px">
    <svg viewBox="0 0 48 48"><rect x="6" y="9" width="36" height="33" rx="2" fill="#1f5fa8"/><rect x="10" y="18" width="28" height="20" fill="#fff"/><g fill="#1f5fa8"><rect x="13" y="21" width="5" height="4"/><rect x="21" y="21" width="5" height="4"/><rect x="29" y="21" width="5" height="4"/><rect x="13" y="29" width="5" height="4"/><rect x="21" y="29" width="5" height="4"/><rect x="29" y="29" width="5" height="4"/></g></svg>
    <div><h3>Same Day Service</h3><p>You deserve a fast solution to your problem. We provide it – right away, with a clear price up front.</p></div>
  </div>
  <div class="feature abs" style="left:98px;top:290px">
    <svg viewBox="0 0 48 48"><path d="M12 22a12 12 0 0124 0z" fill="#1f5fa8"/><rect x="9" y="22" width="30" height="4" fill="#1f5fa8"/><path d="M10 44c0-9 6-14 14-14s14 5 14 14z" fill="#1f5fa8"/></svg>
    <div><h3>Highly Trained Technicians</h3><p>will install or repair your brand air conditioning and heating system for top reliability, energy savings, and property value.</p></div>
  </div>
  <div class="feature abs" style="left:479px;top:290px">
    <svg viewBox="0 0 48 48"><path d="M28 4L12 28h11l-4 16 17-25H25z" fill="#1f5fa8"/></svg>
    <div><h3>Free Energy Survey</h3><p>for replacement air conditioning and heating systems. Let us help you get maximum comfort and savings. No obligation.</p></div>
  </div>
  <div class="why-mascot abs ph" role="img" aria-label="Cartoon technician mascot holding a thermometer and giving a thumbs up"></div>
</section>

<section class="about">
  <div class="video abs">
    <div class="video-art abs ph" role="img" aria-label="Company introduction video still with the mascot and service badge"></div>
    <div class="video-bar abs"><i></i></div>
  </div>
  <h2 class="sec-title">ABOUT OUR COMPANY</h2>
  <div class="about-sub abs">Borvico Heating Services</div>
  <p class="about-text abs" style="top:160px">We are a family owned heating and cooling contractor serving homes and businesses across the valley. Our team installs, repairs and maintains every major system, and we stand behind each job with a clear warranty and friendly follow up.</p>
  <p class="about-text abs" style="top:248px">From new construction to a late night breakdown, we answer the phone and show up on time, ready to work.</p>
  <span class="btn-outline">MORE INFOR ➜</span>
</section>

<section class="services">
  <h2 class="sec-title center-title abs">SERVICES WE PROVIDE</h2>
  <div class="rule abs"></div>

  <div class="svc left abs" style="left:60px;top:136px"><h3>Air Conditioning</h3><p>Installation, service and upkeep for every<br>cooling system, including new homes.</p></div>
  <div class="svc-icon abs" style="left:376px;top:134px"><svg viewBox="0 0 40 40"><rect x="6" y="8" width="28" height="24" rx="2" fill="none" stroke="#fff" stroke-width="2.5"/><circle cx="20" cy="20" r="7" fill="none" stroke="#fff" stroke-width="2.5"/></svg></div>

  <div class="svc left abs" style="left:60px;top:257px"><h3>Heating</h3><p>Gas furnace, two stage furnace and<br>electric heat, fitted and serviced.</p></div>
  <div class="svc-icon abs" style="left:376px;top:255px"><svg viewBox="0 0 40 40"><rect x="5" y="9" width="30" height="22" rx="2" fill="none" stroke="#fff" stroke-width="2.5"/><rect x="11" y="15" width="18" height="10" fill="#fff"/></svg></div>

  <div class="svc left abs" style="left:60px;top:385px"><h3>Duct - Repair</h3><p>Repair, replacement and new duct<br>work, with zoned system options.</p></div>
  <div class="svc-icon abs" style="left:376px;top:383px"><svg viewBox="0 0 40 40"><path d="M6 8h28l-10 12v12l-8-4v-8z" fill="#fff"/></svg></div>

  <div class="van abs ph" role="img" aria-label="Company service van, front view"></div>

  <div class="svc-icon abs" style="left:753px;top:134px"><svg viewBox="0 0 40 40"><g fill="#fff"><rect x="8" y="8" width="4" height="24"/><rect x="15" y="8" width="4" height="24"/><rect x="22" y="8" width="4" height="24"/><rect x="29" y="8" width="4" height="24"/></g></svg></div>
  <div class="svc abs" style="left:849px;top:136px"><h3>Heat pump</h3><p>Efficient heat pump setup and care<br>for steady comfort all year round.</p></div>

  <div class="svc-icon abs" style="left:753px;top:255px"><svg viewBox="0 0 40 40"><g fill="none" stroke="#fff" stroke-width="2.5"><path d="M6 14c5-4 9 4 14 0s9-4 14 0"/><path d="M6 21c5-4 9 4 14 0s9-4 14 0"/><path d="M6 28c5-4 9 4 14 0s9-4 14 0"/></g></svg></div>
  <div class="svc abs" style="left:849px;top:257px"><h3>Hail damage</h3><p>Storm damaged condensers checked,<br>repaired and ready for claims.</p></div>

  <div class="svc-icon abs" style="left:753px;top:383px"><svg viewBox="0 0 40 40"><circle cx="20" cy="20" r="13" fill="none" stroke="#fff" stroke-width="2.5"/><path d="M20 20l6-5" stroke="#fff" stroke-width="2.5"/></svg></div>
  <div class="svc abs" style="left:849px;top:385px"><h3>Thermostats</h3><p>Smart wifi thermostats installed and<br>set up so you control it from anywhere.</p></div>

  <div class="btn-green abs">SCHEDULE AN APPOINTMENT</div>
</section>

<section class="quote-band">
  <div class="quote-mark abs">”</div>
  <p class="quote-text abs">The crew arrived within an hour on a hot Sunday night, found the fault fast and had our air running again before midnight. Fair price, clean work and a friendly tech who explained everything. We will call Borvico for every service from now on and tell our neighbours too.</p>
  <div class="quote-name abs">- Dana, Borvico Heating</div>
  <div class="slide-bars abs"><span class="on"></span><span></span><span></span></div>
</section>

<section class="news">
  <h2 class="sec-title center-title abs">LATEST NEWS</h2>
  <article class="card abs" style="left:98px">
    <div class="card-img ph" role="img" aria-label="Technician servicing an outdoor air conditioning unit" style="background:linear-gradient(135deg,#8a9aa8,#4d5d6c)"></div>
    <span class="date abs">May 20, 2016</span>
    <h4>BORVICO HEATING SERVICES OFFERS MANY DIFFERENT FINANCING</h4>
  </article>
  <article class="card abs" style="left:441px">
    <div class="card-img ph" role="img" aria-label="Workers installing a rooftop condenser unit" style="background:linear-gradient(135deg,#a9b3bc,#5f6b75)"></div>
    <span class="date abs">May 20, 2016</span>
    <h4>BORVICO HEATING SERVICES OFFERS MANY DIFFERENT FINANCING</h4>
  </article>
  <article class="card abs" style="left:783px">
    <div class="card-img ph" role="img" aria-label="Couple reviewing financing paperwork at home" style="background:linear-gradient(135deg,#d8d0c6,#8f7d72)"></div>
    <span class="date abs">May 20, 2016</span>
    <h4>BORVICO HEATING SERVICES OFFERS MANY DIFFERENT FINANCING</h4>
  </article>
</section>

<section class="emergency">
  <div class="em-dark abs"></div>
  <div class="em-thumb abs ph" role="img" aria-label="Cartoon technician mascot"></div>
  <div class="em-title abs">24/7 EMERGENCY CALL : (480) 555-2046</div>
  <div class="em-sub abs">Day or night, a real technician is ready to help,</div>
  <div class="em-btn abs">SCHEDULE AN APPOINTMENT ➜</div>
</section>

<footer class="site-footer">
  <div class="foot-brand abs"><span class="brand-dot"></span><span class="brand-name">Borvico Heating Services</span></div>
  <div class="socials abs"><span></span><span></span><span></span><span></span></div>

  <div class="abs" style="left:372px;top:36px;width:250px">
    <div class="foot-h">SIGN UP FOR NEWSLETTER</div>
    <p class="foot-p" style="margin-top:10px">Get seasonal tips, service reminders and our latest coupons</p>
  </div>
  <div class="field abs">Enter email</div>
  <div class="sub-btn abs">SUBSCRIPTION</div>

  <div class="abs" style="left:703px;top:36px;width:260px">
    <div class="foot-h">CONTACT US</div>
    <div class="contact-row" style="margin-top:18px"><svg viewBox="0 0 16 16"><path d="M8 1a5 5 0 00-5 5c0 4 5 9 5 9s5-5 5-9a5 5 0 00-5-5z" fill="#555"/><circle cx="8" cy="6" r="2" fill="#f3f3f3"/></svg><span>Borvico Heating Services<br>48 Larkfield Row Mesa AZ 85201</span></div>
    <div class="contact-row" style="margin-top:14px"><svg viewBox="0 0 16 16"><path d="M3 2h3l1 3-2 1c1 2 2 3 4 4l1-2 3 1v3C7 13 2 8 3 2z" fill="#555"/></svg><span>Phone: (480) 555-2046</span></div>
    <div class="contact-row" style="margin-top:14px"><svg viewBox="0 0 16 16"><rect x="1" y="3" width="14" height="10" fill="#555"/><path d="M1 3l7 6 7-6" fill="none" stroke="#f3f3f3" stroke-width="1.2"/></svg><span>info@borvicoheating.com</span></div>
  </div>

  <div class="links abs">
    <div class="foot-h">QUICK LINKS</div>
    <ul><li>Home</li><li>About us</li><li>24 hour services</li><li>Coupons</li><li>Financing</li><li>Reviews</li><li>Blog</li><li>Contact us</li></ul>
  </div>
</footer>
<div class="copyright abs" style="left:0;width:1200px">©2015 - 2016 Borvico Heating Services. All Rights Reserved.</div>

</body>
</html>
```